Marlowe Tanbark Beef Jerky Packaging Design

I am chasing a design for our Premium, delicious, hand crafted Beef Jerky.
Packaging Design to be digitally printed on:
Three Side Seal Pouch with Zipper and Hanging Hole
Size: 150mm(width)*200mm(height)
Material Structure: PET/PET(one side metallized)/PA/PE
Thickness: 120micron
Must include all the items listed in the Design Notes - Attached.
Use your creative flare to make it stand out , look awesome but not to busy.

```html
<!DOCTYPE html>
<html lang="en">
<head>
<meta charset="utf-8">
<title>Marlowe Tanbark Beef Jerky – Pouch Range</title>
<link href="https://fonts.googleapis.com/css2?family=Bebas+Neue&family=Montserrat:wght@400;500&display=swap" rel="stylesheet">
<style>
  :root{
    --bg:#eceeed;
    --blue:#1d4f86; --blue-dark:#12375f; --blue-line:#9fd0f2;
    --red:#c8181f; --red-dark:#8f0d12; --red-line:#ff5a5a;
    --brown:#a4502a; --brown-dark:#74361b; --brown-line:#e5875a;
    --white:#f6f4ef;
    --jerky-light:#6a4a32; --jerky-dark:#221510;
    --hole:#ffffff;
  }
  *{box-sizing:border-box;margin:0;padding:0}
  html,body{width:1200px;height:639px;overflow:hidden;background:var(--bg)}
  .range{position:relative;width:1200px;height:639px}
  .pouch{
    position:absolute;top:56px;width:358px;height:530px;
    border-radius:4px 4px 10px 10px;overflow:hidden;
    box-shadow:0 8px 18px rgba(0,0,0,.12);
  }
  .pouch--original{left:54px;background:linear-gradient(160deg,var(--blue) 0%,var(--blue) 45%,var(--blue-dark) 100%);--line:var(--blue-line)}
  .pouch--chilli{left:431px;background:linear-gradient(160deg,var(--red) 0%,var(--red) 50%,var(--red-dark) 100%);--line:var(--red-line)}
  .pouch--smokey{left:802px;background:linear-gradient(160deg,var(--brown) 0%,var(--brown) 50%,var(--brown-dark) 100%);--line:var(--brown-line)}
  .hang-hole{position:absolute;top:30px;left:142px;width:74px;height:15px;border-radius:8px;background:var(--hole)}
  .zipper{position:absolute;top:58px;left:18px;right:18px;height:4px;border-top:1px solid rgba(255,255,255,.18);border-bottom:1px solid rgba(0,0,0,.18)}
  .brand{
    position:absolute;top:132px;left:0;right:0;
    display:flex;align-items:center;justify-content:center;gap:8px;
    font-family:"Bebas Neue",sans-serif;font-size:27px;line-height:1;color:var(--white);letter-spacing:.5px;
  }
  .brand__dot{width:14px;height:14px;border-radius:50%;background:var(--white)}
  .brand__place{
    position:absolute;top:164px;left:0;right:0;text-align:center;
    font-family:"Montserrat",sans-serif;font-size:7px;letter-spacing:2.5px;color:var(--white);opacity:.85;
  }
  .product{
    position:absolute;top:256px;left:0;right:0;text-align:center;
    font-family:"Bebas Neue",sans-serif;font-size:56px;line-height:1;color:var(--white);letter-spacing:1px;
  }
  .flavour{
    position:absolute;top:310px;left:0;right:0;text-align:center;z-index:2;
    font-family:"Bebas Neue",sans-serif;font-size:34px;line-height:1;color:var(--white);
  }
  .window{
    position:absolute;left:129px;top:350px;width:100px;height:178px;
    border:2px solid var(--line);
    border-radius:45% 45% 50% 50% / 22% 22% 78% 78%;
    background:radial-gradient(circle at 45% 35%,var(--jerky-light),var(--jerky-dark) 80%);
  }
  .flavour-cue{position:absolute;left:14px;top:460px;width:100px;height:34px;border-radius:20px}
  .flavour-cue--chilli{background:linear-gradient(90deg,#b01010,#ff7a1a,#ffb347);opacity:.85}
  .flavour-cue--smokey{left:26px;top:440px;width:54px;height:74px;border-radius:30px;background:radial-gradient(circle,rgba(255,235,220,.45),rgba(255,235,220,0) 70%)}
  .web{
    position:absolute;left:6px;bottom:30px;
    font-family:"Montserrat",sans-serif;font-size:9.5px;color:var(--white);
    transform:rotate(5deg);transform-origin:left;
  }
  .weight{
    position:absolute;right:30px;bottom:28px;
    font-family:"Bebas Neue",sans-serif;font-size:22px;color:var(--white);
    transform:rotate(-5deg);
  }
</style>
</head>
<body>
<main class="range">

  <section class="pouch pouch--original" aria-label="Original flavour pouch">
    <div class="hang-hole"></div><div class="zipper"></div>
    <div class="brand"><span class="brand__dot"></span>Marlowe Tanbark Jerky</div>
    <div class="brand__place">TALLOWBY 6830</div>
    <h1 class="product">Beef Jerky</h1>
    <p class="flavour">Original</p>
    <div class="window" role="img" aria-label="Clear window in a bull skull shape showing the beef jerky pieces"></div>
    <p class="web">marlowetanbark.com.au</p>
    <p class="weight">80gm</p>
  </section>

  <section class="pouch pouch--chilli" aria-label="Chilli hot flavour pouch">
    <div class="hang-hole"></div><div class="zipper"></div>
    <div class="brand"><span class="brand__dot"></span>Marlowe Tanbark Jerky</div>
    <div class="brand__place">TALLOWBY 6830</div>
    <h1 class="product">Beef Jerky</h1>
    <p class="flavour">Chili Hot</p>
    <div class="window" role="img" aria-label="Clear window in a bull skull shape showing the beef jerky pieces"></div>
    <div class="flavour-cue flavour-cue--chilli" role="img" aria-label="Flaming red chilli illustration"></div>
    <p class="web">marlowetanbark.com.au</p>
    <p class="weight">80gm</p>
  </section>

  <section class="pouch pouch--smokey" aria-label="Smokey flavour pouch">
    <div class="hang-hole"></div><div class="zipper"></div>
    <div class="brand"><span class="brand__dot"></span>Marlowe Tanbark Jerky</div>
    <div class="brand__place">TALLOWBY 6830</div>
    <h1 class="product">Beef Jerky</h1>
    <p class="flavour">Smokey</p>
    <div class="window" role="img" aria-label="Clear window in a bull skull shape showing the beef jerky pieces"></div>
    <div class="flavour-cue flavour-cue--smokey" role="img" aria-label="Curling smoke wisps illustration"></div>
    <p class="web">marlowetanbark.com.au</p>
    <p class="weight">80gm</p>
  </section>

</main>
</body>
</html>
```